Designer Instructions – Updated Referral Program Flyer

(Based on the mock-up in “Brief Layout and Instructions.pdf”)

OVERALL STYLE + LAYOUT

Maintain the same general layout, structure, and flow as the mock-up flyer (front and back).

This is an update of an older flyer, not a full redesign — keep the same sections, proportions, and overall visual feel, but with cleaner, more modern design improvements.

The final flyer should look clean, bold, professional, and high-impact, geared toward realtors, property managers, and contractors who refer work.

FRONT SIDE INSTRUCTIONS
1. Header Section

Remove the Rebuild Harbor Crest logo from the top banner.
(Shown on page 1 of the PDF)

2. Main Headline

Keep the same three-line structure:
EARN
UNLIMITED
CASH

Center it, maximize impact, and increase the font size of CASH so all three words match in importance.

Make the headline bold, clean, and the main focal point.

3. Cash Incentive Box

Keep the "$500 minimum OR 10% per referral" box, but upgrade the graphics to look sharper and more modern.

Ensure the wording matches exactly what’s in the mock-up.

4. Premier Partner Program Ribbon

Clean up and modernize the "PREMIER PARTNER PROGRAM" bar while keeping the same position and structure.

Ensure the checkmark badge remains crisp and professional.

5. Supporting Icons Section

Keep the four icons/benefit boxes (Guaranteed Payout, Free Evaluations, Affordable Solutions, Industry Leaders) in the same order.

Update the icons to cleaner, more modern styles — but maintain the same meanings.

Improve alignment and spacing for sharper visual consistency.

6. Remove Icons in Contact Area

At the bottom (“CALL TEXT OR BOOK ONLINE 858-471-6093 BrightlaneRenovate.com”), remove the phone and internet icons, as noted on page 2 of the PDF.

7. Replace All Images

I (Dorian) will provide all updated stock images separately via email.

Replace the flood/water-damage imagery and roof leak with the new images I send.

Keep image placement and proportions the same as the mock-up.

BACK SIDE INSTRUCTIONS
1. Header Image + “REFER / EARN” Section

Maintain the same large split-image layout (“The more you refer, the more you earn”).

Replace all background imagery with the new assets I will send.

Keep the CASH FLOW image section but modernize the type and spacing.

2. “HOW IT WORKS” Section

Preserve the three-column layout:

Refer Flood, Water & Mold Damage

We Take Care of Everything (evaluations/insurance)

Get Paid to Share

Update images, tighten spacing, and use modern iconography.

3. Remove Phone/Internet Icons

Same as the front side — remove small communication icons and keep only the text/number/URL.

4. Bottom Contact Bar

Keep the blue bar, same wording, same layout — just modernize the style if needed for clarity.

5. Replace All Back-Side Images

Again, I will email you the image assets.

Keep the layout EXACT — just update with higher-quality photos and improved design.

TEXT CONTENT (Keep as-is unless spacing adjustments needed)

All text shown in the PDF should remain exactly the same unless spacing or visual balance requires minor adjustments.
Example from page 3:

“REFER FLOOD, MOLD & CONSTRUCTION JOBS”

“We Schedule a Free Estimate. If Approved, You Get Paid.”

“Everybody Benefits From Referrals”

Everything stays, just refreshed and visually improved.

DESIGN GOALS

Flyer should look high-end and trustworthy, not salesy.

Consistent color theme: blues, whites, yellows, same palette as original.

Use bold, modern fonts with strong readability.

Ensure all headlines pop and all benefit boxes are clean, well-aligned, and evenly spaced.

The final result should feel like a premium referral program flyer for a top-tier restoration/remodel company.

FILES I WILL PROVIDE

I will send the designer:

All replacement stock photos

Any updated logos (if needed)

Original high-resolution version of the mock-up (if available)

Any additional icons preferred

Colors
0054AA
0677BA
7BADD7
CADEEF
E8F1F8

Requirements
Must have
• Designer Instructions – Updated Referral Program Flyer (Based on the mock-up in “Brief Layout and Instructions.pdf”) OVERALL STYLE + LAYOUT Maintain the same general layout, structure, and flow as the mock-up flyer (front and back). This is an update of an older flyer, not a full redesign — keep the same sections, proportions, and overall visual feel, but with cleaner, more modern design improvements. The final flyer should look clean, bold, professional, and high-impact, geared toward realtors, property managers, and contractors who refer work. FRONT SIDE INSTRUCTIONS 1. Header Section Remove the Rebuild Harbor Crest logo from the top banner. (Shown on page 1 of the PDF) 2. Main Headline Keep the same three-line structure: EARN UNLIMITED CASH Center it, maximize impact, and increase the font size of CASH so all three words match in importance. Make the headline bold, clean, and the main focal point. 3. Cash Incentive Box Keep the "$500 minimum OR 10% per referral" box, but upgrade the graphics to look sharper and more modern. Ensure the wording matches exactly what’s in the mock-up. 4. Premier Partner Program Ribbon Clean up and modernize the "PREMIER PARTNER PROGRAM" bar while keeping the same position and structure. Ensure the checkmark badge remains crisp and professional. 5. Supporting Icons Section Keep the four icons/benefit boxes (Guaranteed Payout, Free Evaluations, Affordable Solutions, Industry Leaders) in the same order. Update the icons to cleaner, more modern styles — but maintain the same meanings. Improve alignment and spacing for sharper visual consistency. 6. Remove Icons in Contact Area At the bottom (“CALL TEXT OR BOOK ONLINE 858-471-6093 BrightlaneRenovate.com”), remove the phone and internet icons, as noted on page 2 of the PDF. 7. Replace All Images I (Dorian) will provide all updated stock images separately via email. Replace the flood/water-damage imagery and roof leak with the new images I send. Keep image placement and proportions the same as the mock-up. BACK SIDE INSTRUCTIONS 1. Header Image + “REFER / EARN” Section Maintain the same large split-image layout (“The more you refer, the more you earn”). Replace all background imagery with the new assets I will send. Keep the CASH FLOW image section but modernize the type and spacing. 2. “HOW IT WORKS” Section Preserve the three-column layout: Refer Flood, Water & Mold Damage We Take Care of Everything (evaluations/insurance) Get Paid to Share Update images, tighten spacing, and use modern iconography. 3. Remove Phone/Internet Icons Same as the front side — remove small communication icons and keep only the text/number/URL. 4. Bottom Contact Bar Keep the blue bar, same wording, same layout — just modernize the style if needed for clarity. 5. Replace All Back-Side Images Again, I will email you the image assets. Keep the layout EXACT — just update with higher-quality photos and improved design. TEXT CONTENT (Keep as-is unless spacing adjustments needed) All text shown in the PDF should remain exactly the same unless spacing or visual balance requires minor adjustments. Example from page 3: “REFER FLOOD, MOLD & CONSTRUCTION JOBS” “We Schedule a Free Estimate. If Approved, You Get Paid.” “Everybody Benefits From Referrals” Everything stays, just refreshed and visually improved. DESIGN GOALS Flyer should look high-end and trustworthy, not salesy. Consistent color theme: blues, whites, yellows, same palette as original. Use bold, modern fonts with strong readability. Ensure all headlines pop and all benefit boxes are clean, well-aligned, and evenly spaced. The final result should feel like a premium referral program flyer for a top-tier restoration/remodel company. FILES I WILL PROVIDE I will send the designer: All replacement stock photos Any updated logos (if needed) Original high-resolution version of the mock-up (if available) Any additional icons preferred

```html
<!DOCTYPE html>
<html lang="en">
<head>
<meta charset="utf-8">
<title>Premier Partner Referral Program Flyer</title>
<link href="https://fonts.googleapis.com/css2?family=Alfa+Slab+One&family=Anton&family=Lexend:wght@300;400;600&family=Montserrat:ital,wght@0,400;0,600;0,700;0,800;0,900;1,800;1,900&display=swap" rel="stylesheet">
<style>
  :root {
    --stage: #45484e;
    --brand-blue: #1b4fa0;
    --bright-blue: #3b7fd6;
    --deep-navy: #121a2b;
    --heading-navy: #1f2f6b;
    --alert-red: #d9383a;
    --sun-yellow: #f9cc12;
    --ink: #141414;
    --body-text: #2a2a2a;
    --paper: #ffffff;
    --soft-line: #d9dbe0;
  }
  * { box-sizing: border-box; margin: 0; padding: 0; }
  html, body { width: 1200px; height: 1200px; overflow: hidden; }
  body { background: var(--stage); position: relative; font-family: "Lexend", sans-serif; }

  .card { position: absolute; left: 192px; width: 815px; height: 528px; background: var(--paper); overflow: hidden; }
  .card--front { top: 52px; }
  .card--back { top: 620px; }

  .card-art { position: absolute; inset: 0; width: 815px; height: 528px; }

  .photo-skyline {
    position: absolute; left: 360px; top: 0; width: 455px; height: 263px;
    background: linear-gradient(180deg, #8a77c3 0%, #b887bd 30%, #d59a9a 50%, #e3a46e 60%, #6a5d9c 70%, #4a4c8c 100%);
  }
  .photo-cash {
    position: absolute; left: 370px; top: 0; width: 445px; height: 263px;
    clip-path: polygon(99px 0, 100% 0, 100% 100%, 0 100%);
    background: linear-gradient(135deg, #e3e5df 0%, #b5bbb2 40%, #8fc9cf 55%, #c9cdc5 75%, #e8e9e4 100%);
  }

  .benefit {
    position: absolute; top: 337px; width: 178px; height: 121px;
    background: var(--paper); border-radius: 10px;
    box-shadow: 0 3px 10px rgba(0,0,0,0.16);
    text-align: center; padding-top: 35px;
  }
  .benefit__icon {
    position: absolute; left: 59px; top: -30px; width: 60px; height: 60px;
    border-radius: 50%; background: var(--paper);
    box-shadow: 0 3px 0 #c9ccd2, 0 2px 6px rgba(0,0,0,0.18);
    display: flex; align-items: center; justify-content: center;
  }
  .benefit__title {
    font-family: "Montserrat", sans-serif; font-weight: 800; font-size: 16px; line-height: 20px;
    color: var(--heading-navy); letter-spacing: 0.3px;
  }
  .benefit__text {
    margin-top: 3px; font-size: 10.5px; line-height: 12.5px; color: var(--body-text); letter-spacing: 0.2px;
  }

  .contact-label {
    position: absolute; left: 29px; top: 491px; font-family: "Montserrat", sans-serif;
    font-weight: 800; font-size: 13.5px; letter-spacing: 0.6px; color: var(--paper); line-height: 1;
  }
  .contact-label .contact-or { font-weight: 400; }
  .contact-phone {
    position: absolute; left: 304px; top: 487px; font-family: "Montserrat", sans-serif;
    font-weight: 900; font-size: 26px; line-height: 1; color: var(--ink); letter-spacing: 0.2px;
  }
  .contact-divider { position: absolute; left: 536px; top: 483px; width: 1px; height: 37px; background: var(--ink); }
  .contact-url {
    position: absolute; left: 566px; top: 492px; font-size: 14.2px; line-height: 1; color: var(--ink); letter-spacing: 0.3px;
  }

  .step-heading {
    position: absolute; top: 283px; font-family: "Montserrat", sans-serif; font-weight: 800;
    font-size: 16px; line-height: 20px; color: var(--heading-navy); letter-spacing: 0.3px; white-space: nowrap;
  }
  .step-divider { position: absolute; top: 282px; width: 1.5px; height: 173px; background: var(--soft-line); }
  .step-visual { position: absolute; top: 347px; width: 104px; height: 104px; border-radius: 50%; }
  .step-visual--badge { left: 38px; border: 7px solid var(--alert-red); background: var(--paper); }
  .step-visual--inspection { left: 288px; background: linear-gradient(160deg, #9fc6e6 0%, #eef0ee 45%, #6f8f5c 70%, #3f6fa8 100%); }
  .step-visual--sign { left: 557px; background: radial-gradient(circle at 50% 50%, #f6d21b 0 38%, #8fb6df 39% 100%); }
  .step-copy {
    position: absolute; top: 365px; font-size: 10.5px; line-height: 15px; color: var(--body-text); letter-spacing: 0.2px;
  }
  .step-copy b { font-weight: 600; }
</style>
</head>
<body>

<section class="card card--front" aria-label="Front: Earn Unlimited Cash">
  <div class="photo-skyline" role="img" aria-label="Photo of a city skyline at dusk across the water"></div>

  <svg class="card-art" viewBox="0 0 815 528" xmlns="http://www.w3.org/2000/svg">
    <defs>
      <radialGradient id="heroBlue" cx="0.25" cy="0.4" r="0.9">
        <stop offset="0" stop-color="#4f95e4"/>
        <stop offset="0.55" stop-color="#2a62b8"/>
        <stop offset="1" stop-color="#1b4fa0"/>
      </radialGradient>
    </defs>
    <polyline points="371,-2 431,128 375,265" fill="none" stroke="var(--sun-yellow)" stroke-width="14"/>
    <polyline points="358,-2 418,128 362,265" fill="none" stroke="#fff" stroke-width="6"/>
    <polygon points="0,0 352,0 412,128 356,263 0,263" fill="url(#heroBlue)"/>

    <g transform="translate(15,0) skewX(-6)" font-family="Alfa Slab One, serif" text-anchor="middle">
      <g fill="none" stroke="#fff" stroke-width="30" stroke-linejoin="round" aria-hidden="true">
        <text x="208" y="100" font-size="62" textLength="192" lengthAdjust="spacingAndGlyphs">EARN</text>
        <text x="208" y="137" font-size="42" textLength="248" lengthAdjust="spacingAndGlyphs">UNLIMITED</text>
        <text x="208" y="191" font-size="64" textLength="183" lengthAdjust="spacingAndGlyphs">CA$H</text>
      </g>
      <g fill="none" stroke="var(--ink)" stroke-width="18" stroke-linejoin="round" aria-hidden="true">
        <text x="208" y="100" font-size="62" textLength="192" lengthAdjust="spacingAndGlyphs">EARN</text>
        <text x="208" y="137" font-size="42" textLength="248" lengthAdjust="spacingAndGlyphs">UNLIMITED</text>
        <text x="208" y="191" font-size="64" textLength="183" lengthAdjust="spacingAndGlyphs">CA$H</text>
      </g>
      <text x="208" y="100" font-size="62" textLength="192" lengthAdjust="spacingAndGlyphs" fill="var(--sun-yellow)">EARN</text>
      <text x="208" y="137" font-size="42" textLength="248" lengthAdjust="spacingAndGlyphs" fill="#fff">UNLIMITED</text>
      <text x="208" y="191" font-size="64" textLength="183" lengthAdjust="spacingAndGlyphs" fill="var(--sun-yellow)">CA$H</text>
    </g>

    <polygon points="0,235 348,235 330,292 0,292" fill="var(--alert-red)"/>
    <g font-family="Montserrat, sans-serif" font-style="italic" fill="#fff">
      <text x="36" y="268" font-size="30" font-weight="900" textLength="79" lengthAdjust="spacingAndGlyphs">$500</text>
      <text x="45" y="282" font-size="11" font-weight="800" textLength="61" lengthAdjust="spacingAndGlyphs">MINIMUM</text>
      <text x="188" y="277" font-size="30" font-weight="900" textLength="53" lengthAdjust="spacingAndGlyphs">10%</text>
      <text x="252" y="262" font-size="12.5" font-weight="800" textLength="27" lengthAdjust="spacingAndGlyphs">PER</text>
      <text x="248" y="277" font-size="12.5" font-weight="800" textLength="70" lengthAdjust="spacingAndGlyphs">REFERRAL</text>
    </g>
    <polygon points="126,248 180,248 172,280 118,280" fill="#fff"/>
    <text x="149" y="272" text-anchor="middle" font-family="Montserrat, sans-serif" font-weight="800" font-size="21" fill="var(--ink)">or</text>

    <text x="601" y="232" text-anchor="middle" font-family="Lexend, sans-serif" font-weight="300" font-size="17" letter-spacing="8" fill="#fff">PREMIER</text>
    <rect x="421" y="242" width="357" height="44" rx="22" fill="#1c1c1c"/>
    <path d="M443,242 H592 V286 H443 A22 22 0 0 1 443,242 Z" fill="var(--alert-red)"/>
    <g font-family="Montserrat, sans-serif" font-weight="800" font-size="28" fill="#fff">
      <text x="438" y="275" textLength="118" lengthAdjust="spacingAndGlyphs">PARTNER</text>
      <text x="628" y="275" textLength="134" lengthAdjust="spacingAndGlyphs">PROGRAM</text>
    </g>
    <path d="M593,239 C600,245 610,247 617,246 V262 C617,276 606,285 593,291 C580,285 569,276 569,262 V246 C576,247 586,245 593,239 Z" fill="#fff" stroke="#e9e9e9" stroke-width="1"/>
    <polyline points="581,263 590,272 606,252" fill="none" stroke="var(--alert-red)" stroke-width="5" stroke-linecap="round" stroke-linejoin="round"/>

    <polygon points="0,475 270,475 255,528 0,528" fill="var(--brand-blue)"/>
  </svg>

  <div class="benefit" style="left:37px">
    <div class="benefit__icon">
      <svg width="34" height="34" viewBox="0 0 34 34"><path d="M17,2 L21,5 L26,4 L27,9 L31,12 L29,17 L31,22 L27,25 L26,30 L21,29 L17,32 L13,29 L8,30 L7,25 L3,22 L5,17 L3,12 L7,9 L8,4 L13,5 Z" fill="var(--heading-navy)"/><circle cx="17" cy="17" r="9" fill="none" stroke="#fff" stroke-width="2"/><polyline points="12.5,17 16,20.5 21.5,14" fill="none" stroke="#fff" stroke-width="2.4" stroke-linecap="round" stroke-linejoin="round"/></svg>
    </div>
    <div class="benefit__title">GUARANTEED<br>PAYOUT</div>
    <div class="benefit__text">Minimum $500 or 10% of<br>Total Invoice Paid Fast</div>
  </div>

  <div class="benefit" style="left:226px">
    <div class="benefit__icon">
      <svg width="34" height="34" viewBox="0 0 34 34"><rect x="4" y="3" width="20" height="28" rx="2" fill="var(--heading-navy)"/><rect x="7" y="6" width="14" height="6" fill="#fff"/><g fill="#fff"><rect x="7" y="15" width="3.5" height="3"/><rect x="12.2" y="15" width="3.5" height="3"/><rect x="17.4" y="15" width="3.5" height="3"/><rect x="7" y="20" width="3.5" height="3"/><rect x="12.2" y="20" width="3.5" height="3"/><rect x="17.4" y="20" width="3.5" height="3"/><rect x="7" y="25" width="3.5" height="3"/><rect x="12.2" y="25" width="3.5" height="3"/></g><circle cx="26" cy="20" r="6" fill="#fff" stroke="var(--heading-navy)" stroke-width="2"/><text x="26" y="23" text-anchor="middle" font-family="Montserrat, sans-serif" font-weight="800" font-size="8" fill="var(--heading-navy)">$</text><rect x="20" y="27" width="12" height="4" rx="1" fill="var(--heading-navy)"/></svg>
    </div>
    <div class="benefit__title">FREE<br>ESTIMATES</div>
    <div class="benefit__text">Fast &amp; Free Inspections<br>&amp; Written Estimates</div>
  </div>

  <div class="benefit" style="left:414px">
    <div class="benefit__icon">
      <svg width="34" height="34" viewBox="0 0 34 34"><path d="M18,3 C22,8 25,11 25,15 A7,7 0 0 1 11,15 C11,11 14,8 18,3 Z" fill="var(--heading-navy)"/><text x="18" y="18.5" text-anchor="middle" font-family="Montserrat, sans-serif" font-weight="800" font-size="9" fill="#fff">$</text><path d="M3,24 L9,21 C11,20 13,20 15,21 L21,22 C23,22.5 23,25 21,25 L15,25 L22,26 L29,22 C31,21 32,23 31,24 L23,30 L12,31 L3,30 Z" fill="var(--heading-navy)"/></svg>
    </div>
    <div class="benefit__title">AFFORDABLE<br>SOLUTIONS</div>
    <div class="benefit__text">Lowest Out of Pocket Costs<br>for Your Customers</div>
  </div>

  <div class="benefit" style="left:603px">
    <div class="benefit__icon">
      <svg width="36" height="34" viewBox="0 0 36 34"><circle cx="18" cy="9" r="6" fill="none" stroke="var(--heading-navy)" stroke-width="3" stroke-dasharray="3 1.7"/><circle cx="18" cy="9" r="2.5" fill="var(--heading-navy)"/><circle cx="7" cy="17" r="3.5" fill="var(--heading-navy)"/><circle cx="29" cy="17" r="3.5" fill="var(--heading-navy)"/><circle cx="18" cy="21" r="4" fill="var(--heading-navy)"/><path d="M1,28 A6,6 0 0 1 13,28 Z M23,28 A6,6 0 0 1 35,28 Z M10,33 A8,7 0 0 1 26,33 Z" fill="var(--heading-navy)"/></svg>
    </div>
    <div class="benefit__title">INDUSTRY<br>LEADERS</div>
    <div class="benefit__text">Licensed &amp; Certified Experts<br>Provide 100% Guarante</div>
  </div>

  <div class="contact-label">CALL, TEXT <span class="contact-or">OR</span> BOOK ONLINE</div>
  <div class="contact-phone">858-471-6093</div>
  <div class="contact-divider"></div>
  <div class="contact-url">www.BrightlaneRenovate.com</div>
</section>

<section class="card card--back" aria-label="Back: How it works">
  <div class="photo-cash" role="img" aria-label="Photo of dollar bills with letter tiles spelling CASH FLOW"></div>

  <svg class="card-art" viewBox="0 0 815 528" xmlns="http://www.w3.org/2000/svg">
    <defs>
      <radialGradient id="backBlue" cx="0.15" cy="0.2" r="0.9">
        <stop offset="0" stop-color="#4f95e4"/>
        <stop offset="0.5" stop-color="#2a62b8"/>
        <stop offset="1" stop-color="#1b4fa0"/>
      </radialGradient>
      <linearGradient id="redFade" x1="0" y1="0" x2="1" y2="0">
        <stop offset="0" stop-color="#d9383a" stop-opacity="0"/>
        <stop offset="0.6" stop-color="#d9383a" stop-opacity="0.9"/>
        <stop offset="1" stop-color="#d9383a"/>
      </linearGradient>
      <linearGradient id="goldText" x1="0" y1="0" x2="0" y2="1">
        <stop offset="0" stop-color="#fbe11a"/>
        <stop offset="1" stop-color="#f7901e"/>
      </linearGradient>
    </defs>
    <polygon points="0,0 469,0 370,263 0,263" fill="url(#backBlue)"/>
    <polygon points="240,57 453,57 403,191 240,191" fill="url(#redFade)"/>
    <polygon points="0,67 24,29 165,29 165,110 224,110 224,205 214,214 0,214" fill="var(--deep-navy)"/>

    <g font-family="Anton, sans-serif">
      <text x="35" y="57" font-size="25" textLength="126" lengthAdjust="spacingAndGlyphs" fill="#fff">THE MORE YOU</text>
      <text x="35" y="108" font-size="56" textLength="126" lengthAdjust="spacingAndGlyphs" fill="url(#goldText)">REFER</text>
      <text x="98" y="133" font-size="23" textLength="124" lengthAdjust="spacingAndGlyphs" fill="#fff">THE MORE YOU</text>
      <text x="98" y="195" font-size="60" textLength="124" lengthAdjust="spacingAndGlyphs" fill="url(#goldText)">EARN</text>
    </g>

    <rect x="261" y="37" width="117" height="38" rx="19" fill="var(--alert-red)"/>
    <g font-family="Alfa Slab One, serif" fill="#fff" text-anchor="middle">
      <text x="320" y="63" font-size="18" letter-spacing="1">REFER</text>
      <text x="320" y="107" font-size="18">FLOODS,</text>
      <text x="320" y="127" font-size="18">REMODELS,</text>
      <text x="320" y="147" font-size="18" textLength="154" lengthAdjust="spacingAndGlyphs">RENOVATIONS</text>
      <text x="320" y="167" font-size="18">&amp; REPAIRS</text>
    </g>

    <polygon points="0,214 317,214 298,263 0,263" fill="var(--sun-yellow)"/>
    <text x="35" y="252" font-family="Montserrat, sans-serif" font-weight="800" font-size="29" textLength="233" lengthAdjust="spacingAndGlyphs" fill="var(--ink)">HOW IT WORKS</text>

    <polygon points="0,475 270,475 255,528 0,528" fill="var(--brand-blue)"/>
  </svg>

  <div class="step-heading" style="left:35px">REFER FLOOD, MOLD<br>&amp; CONSTRUCTIONJOBS</div>
  <div class="step-heading" style="left:288px">WE TAKE CARE<br>OF EVERYTHING</div>
  <div class="step-heading" style="left:555px">EVERYBODY BENEFITS<br>FROM REFERRALS</div>
  <div class="step-divider" style="left:263px"></div>
  <div class="step-divider" style="left:533px"></div>

  <div class="step-visual step-visual--badge" role="img" aria-label="24 hour emergency service badge"></div>
  <div class="step-visual step-visual--inspection" role="img" aria-label="Photo of an inspector with a clipboard in front of a house"></div>
  <div class="step-visual step-visual--sign" role="img" aria-label="Yellow road sign reading Get Paid to Share against a blue sky"></div>

  <div class="step-copy" style="left:165px">It's Simple<br>to <b>Refer 24/7</b>:<br>Call, Text or<br>Book Online.</div>
  <div class="step-copy" style="left:417px">We Schedule<br>a <b>Free Estimate.</b><br>If Approved,<br>You Get Paid.</div>
  <div class="step-copy" style="left:686px">We Provide<br>Expert Quality<br>Work for<br><b>Affordable</b> Price.</div>

  <div class="contact-label">CALL, TEXT <span class="contact-or">OR</span> BOOK ONLINE</div>
  <div class="contact-phone">858-471-6093</div>
  <div class="contact-divider"></div>
  <div class="contact-url">www.BrightlaneRenovate.com</div>
</section>

</body>
</html>
```